Business card por a urban DJ, up scale audience target

Need a sober design, modern, conservative colors but i can consider some options, y play rnb, hip hop, EDM and top40.

Business card for contact and personal info, double sided, use logo attrached please; im 42 so i need a card acording to my age an target audience.

Target Market(s)

Adult people, up scale audience

Industry/Entity Type

Music Download

Contact Information for Business Card

Cel (318) 4207265518 www.lumadrift.com

Requirements
Must have
• open mind
Nice to have
• open mind
Should not have
• DJ

```html
<!DOCTYPE html>
<html lang="en">
<head>
<meta charset="utf-8">
<title>Lumadrift Business Card</title>
<link rel="stylesheet" href="https://fonts.googleapis.com/css2?family=Open+Sans:wght@400;600;800&display=swap">
<style>
  :root {
    --stage: #2c2e32;
    --card-dark: #2a2a2a;
    --card-light: #ffffff;
    --ink: #1f1f1f;
    --ink-soft: #555555;
    --rule: #b5b5b5;
    --logo-light: #ffffff;
  }
  * { margin: 0; padding: 0; box-sizing: border-box; }
  html, body { width: 1200px; height: 864px; overflow: hidden; }
  body {
    background: var(--stage);
    font-family: "Open Sans", Arial, sans-serif;
    position: relative;
  }
  .card {
    position: absolute;
    width: 560px;
    height: 320px;
    left: 320px;
    border-radius: 3px;
  }
  .card--back { top: 70px; background: var(--card-dark); }
  .card--front { top: 460px; background: var(--card-light); color: var(--ink); }

  .brand {
    position: absolute;
    display: flex;
    align-items: center;
    gap: 10px;
    font-weight: 800;
    letter-spacing: 2px;
    line-height: 1;
  }
  .brand__mark { display: block; }
  .card--back .brand {
    left: 50%; top: 50%;
    transform: translate(-50%, -50%);
    color: var(--logo-light);
    font-size: 64px;
  }
  .card--back .brand__mark { width: 18px; height: 18px; background: var(--logo-light); }
  .card--front .brand {
    right: 34px; top: 62px;
    color: var(--ink);
    font-size: 54px;
  }
  .card--front .brand__mark { width: 15px; height: 15px; background: var(--ink); }

  .holder { position: absolute; left: 24px; top: 112px; }
  .holder__name { font-size: 19px; font-weight: 600; }
  .holder__role { font-size: 11.5px; color: var(--ink-soft); margin-top: -2px; }

  .rule {
    position: absolute;
    left: 24px; right: 34px; top: 160px;
    border-top: 1px solid var(--rule);
  }

  .contacts {
    position: absolute;
    right: 30px; top: 190px;
    list-style: none;
    text-align: right;
    font-size: 13px;
    line-height: 19px;
  }
  .contacts li { display: flex; justify-content: flex-end; align-items: center; gap: 10px; }
  .contacts svg { width: 11px; height: 11px; fill: var(--ink); flex: none; }
</style>
</head>
<body>
  <section class="card card--back" aria-label="Card back">
    <div class="brand"><span class="brand__mark"></span>LUMA</div>
  </section>

  <section class="card card--front" aria-label="Card front">
    <div class="brand"><span class="brand__mark"></span>LUMA</div>
    <div class="holder">
      <p class="holder__name">Marcus Bell</p>
      <p class="holder__role">Managing Director</p>
    </div>
    <div class="rule"></div>
    <ul class="contacts">
      <li>(318) 4207265518
        <svg viewBox="0 0 12 12"><path d="M2.4 0.6l2 2.2-1 1.3c.7 1.5 1.9 2.8 3.5 3.5l1.3-1 2.2 2-1 2.2C5 10.6 1.4 7 0.4 1.6z"/></svg></li>
      <li>(318) 4207265519
        <svg viewBox="0 0 12 12"><path d="M3 1h5v3H3zM1 4.5h10v6H1zM3 7h6v1H3z"/></svg></li>
      <li>(318) 4207265519
        <svg viewBox="0 0 12 12"><path d="M3 0h6v12H3zM4 1.5v7.5h4V1.5zM5.5 10h1v1h-1z" fill-rule="evenodd"/></svg></li>
      <li>info@lumadrift.com
        <svg viewBox="0 0 12 12"><path d="M0 2h12v8H0zM0.8 2.8l5.2 3.8 5.2-3.8v-.3H0.8z" fill-rule="evenodd"/></svg></li>
      <li>www.lumadrift.com
        <svg viewBox="0 0 12 12"><path d="M5 7l2-2M4.5 5.5L2.5 7.5a1.8 1.8 0 0 0 2.5 2.5l2-2M7.5 6.5l2-2A1.8 1.8 0 0 0 7 2L5 4" fill="none" stroke="#1f1f1f" stroke-width="1.3" stroke-linecap="round"/></svg></li>
    </ul>
  </section>
</body>
</html>
```